Sign for Truck Parking Company

We do not like the proposed solution of a local signage company.

We need to use the existing sign in terms of size. We want to use our logo, tag line "Nationwide Trailer Parking Solutions", show our phone as (970) BRELMAX & (970) 555-0143, our address of 2840 Alder and our url of halvenmoorgroup.com. We want to make sure the fonts match our corporate logo as best as possible. We don't like the current layout as the fonts don't match and it looks very busy. You can assume that the base will be painted black. Can we make “Nationwide Trailer Parking Solutions” roughly the same font, size and color as the URL (and maybe make it the same size and font and color as “Companies” by shrinking the logo a little).I think on the phone number, its letter equivalent can be on the bottom portion. We are up for a variety of options and want to maintain our fonts and colors. Thanks!

```html
<!DOCTYPE html>
<html lang="en">
<head>
<meta charset="utf-8">
<title>Halvenmoor Group – Site Sign</title>
<link rel="stylesheet" href="https://fonts.googleapis.com/css2?family=Krona+One&display=swap">
<style>
  :root {
    --sign-black: #000000;
    --panel-white: #ffffff;
    --brand-gray: #6d6e71;
    --brand-blue: #2b5ca8;
    --page-bg: #ffffff;
  }
  html, body {
    margin: 0;
    padding: 0;
    width: 1200px;
    height: 1200px;
    overflow: hidden;
    background: var(--page-bg);
  }
  .canvas {
    display: block;
    width: 1200px;
    height: 1200px;
  }
  .sign-text {
    font-family: "Krona One", "Arial Black", sans-serif;
  }
  .brand-name { fill: var(--brand-gray); font-size: 38px; }
  .tagline { fill: var(--panel-white); font-size: 27px; text-anchor: end; }
  .phone-line { fill: var(--panel-white); font-size: 25px; letter-spacing: 1px; }
  .web-address { fill: var(--brand-gray); font-size: 22px; letter-spacing: 2px; }
  .street-address { fill: var(--panel-white); font-size: 25px; letter-spacing: 1px; }
</style>
</head>
<body>
<svg class="canvas" viewBox="0 0 1500 1500" xmlns="http://www.w3.org/2000/svg" aria-label="Site sign for Halvenmoor Group">
  <g class="sign">
    <!-- cabinet -->
    <rect class="sign-cabinet" x="357" y="153" width="786" height="505" fill="var(--sign-black)"/>

    <!-- upper face -->
    <rect class="upper-face" x="372" y="173" width="756" height="364" fill="var(--panel-white)"/>
    <polygon class="upper-gray-field" points="742,173 1128,173 1128,520 395,520 420,470 867,470" fill="var(--brand-gray)"/>
    <rect class="upper-frame" x="389.5" y="194.5" width="721" height="325" fill="none" stroke="var(--brand-blue)" stroke-width="3"/>

    <!-- brand name -->
    <rect class="brand-square" x="417" y="300" width="22" height="22" fill="var(--brand-blue)"/>
    <text class="sign-text brand-name" x="452" y="324" textLength="310" lengthAdjust="spacingAndGlyphs">HALVENMOOR</text>
    <text class="sign-text brand-name" x="417" y="421" textLength="345" lengthAdjust="spacingAndGlyphs">GROUP</text>

    <!-- tagline -->
    <text class="sign-text tagline" x="1088" y="290">NATIONWIDE</text>
    <text class="sign-text tagline" x="1088" y="328">TRAILER</text>
    <text class="sign-text tagline" x="1088" y="366">PARKING</text>
    <text class="sign-text tagline" x="1088" y="404">SOLUTIONS</text>

    <!-- phone band -->
    <text class="sign-text phone-line" x="433" y="507" textLength="652" lengthAdjust="spacingAndGlyphs">(970) BRELMAX • (970) 555-0143</text>

    <!-- lower face -->
    <rect class="lower-face" x="372" y="549" width="756" height="96" fill="var(--panel-white)"/>
    <polygon class="address-field" points="860,549 1128,549 1128,645 820,645" fill="var(--brand-blue)"/>
    <text class="sign-text web-address" x="403" y="607" textLength="427" lengthAdjust="spacingAndGlyphs">halvenmoorgroup.com</text>
    <text class="sign-text street-address" x="889" y="608" textLength="197" lengthAdjust="spacingAndGlyphs">2840 Alder</text>
  </g>
</svg>
</body>
</html>
```